Pebble Tracks - explore habits of productive people

Pebble Tracks is a social place around habits and productivity

The full brief below:

https://notes.brimwellpad.net/page/d/7Qx-RtVmPLa93KwBz-H-cNmq2YeTsRfvUdGkHpXwaB/view?mode=shared

Colors

Designer to choose colors to be used in the design.

Requirements
Must have
• - a feed page to display habits
• - a habit page to add a habit
• / clean, no cluttered design, lots of white space
• / inspired by material design or other design system
Nice to have
• - user page

```html
<!DOCTYPE html>
<html lang="en">
<head>
<meta charset="utf-8">
<title>Pebble Tracks — Feed</title>
<link rel="stylesheet" href="https://fonts.googleapis.com/css2?family=Montserrat:wght@300;400;500;600;700&display=swap">
<style>
  :root {
    --page-bg: #eef0f3;
    --bar-bg: #262626;
    --card-bg: #ffffff;
    --border: #dcdfe3;
    --ink: #2f2f2f;
    --muted: #8a8a8a;
    --accent: #1b8fd1;
    --icon-grey: #9a9a9a;
    --footer-ink: #e2e2e2;
  }
  * { box-sizing: border-box; margin: 0; padding: 0; }
  html, body { width: 1200px; height: 2253px; overflow: hidden; }
  body {
    background: var(--page-bg);
    font-family: "Montserrat", Arial, sans-serif;
    color: var(--ink);
    position: relative;
  }

  /* Top bar */
  .top-bar {
    position: absolute; left: 0; top: 0; width: 1200px; height: 104px;
    background: var(--bar-bg);
  }
  .brand {
    position: absolute; left: 32px; top: 34px;
    font-size: 30px; font-weight: 600; color: #fff; letter-spacing: .5px;
  }
  .account { position: absolute; right: 30px; top: 20px; display: flex; align-items: center; }
  .account-name { color: #fff; font-size: 19px; font-weight: 700; margin-right: 12px; letter-spacing: .3px; }
  .account-avatar {
    width: 65px; height: 65px; border-radius: 50%;
    background: radial-gradient(circle at 50% 40%, #b58d72, #5d4a3e);
  }
  .add-button {
    width: 52px; height: 52px; border-radius: 50%; margin-left: 6px;
    border: 2px solid #6a6a6a; display: flex; align-items: center; justify-content: center;
  }

  /* Feed panel */
  .feed-panel {
    position: absolute; left: 67px; top: 161px; width: 1067px; height: 1924px;
    background:
      linear-gradient(135deg, rgba(210,236,244,.55) 0%, rgba(255,255,255,0) 35%),
      linear-gradient(225deg, rgba(200,234,240,.6) 0%, rgba(255,255,255,0) 40%),
      linear-gradient(180deg, #f6fbfd 0%, #ffffff 100%);
    box-shadow: 0 1px 4px rgba(0,0,0,.06);
  }
  .feed-title {
    position: absolute; left: 0; width: 100%; top: 38px;
    text-align: center; font-size: 52px; font-weight: 400; letter-spacing: 2px; color: #3a3a3a;
  }
  .post-list { position: absolute; left: 122px; top: 128px; width: 823px; }

  .post {
    position: relative; background: var(--card-bg);
    border: 1px solid var(--border); border-radius: 3px; height: 283px;
  }
  .post + .post { margin-top: 46px; }
  .post.has-media { height: 600px; }
  .post-author { position: absolute; left: 24px; top: 21px; display: flex; align-items: center; }
  .avatar { width: 63px; height: 63px; border-radius: 50%; }
  .avatar.tone-1 { background: radial-gradient(circle at 50% 40%, #b48a6e, #4e3f35); }
  .avatar.tone-2 { background: radial-gradient(circle at 50% 40%, #c79473, #4a2f22); }
  .avatar.tone-3 { background: radial-gradient(circle at 50% 40%, #d9b393, #6e5644); }
  .avatar.tone-4 { background: radial-gradient(circle at 50% 40%, #bf8e6e, #3d3029); }
  .author-info { margin-left: 21px; }
  .author-name { font-size: 17px; font-weight: 700; letter-spacing: .3px; color: #262626; }
  .post-meta { margin-top: 11px; font-family: Arial, sans-serif; font-size: 15px; color: var(--muted); }
  .post-text { position: absolute; left: 24px; top: 117px; font-size: 16px; color: #333; }
  .post-media {
    position: absolute; left: 25px; top: 161px; width: 771px; height: 303px;
    background:
      radial-gradient(ellipse at 48% 70%, rgba(255,236,210,.55) 0%, rgba(255,236,210,0) 35%),
      radial-gradient(ellipse at 40% 40%, #8a5a44 0%, #3a2622 55%, #201716 100%);
  }
  .post-actions { position: absolute; left: 24px; top: 168px; display: flex; }
  .has-media .post-actions { top: 489px; }
  .action {
    display: flex; align-items: center; gap: 10px;
    color: var(--accent); font-size: 16px; font-weight: 500; margin-right: 44px;
  }
  .comment-bar {
    position: absolute; left: 0; right: 0; bottom: 0; height: 65px;
    border-top: 1px solid var(--border);
    display: flex; align-items: center; justify-content: space-between; padding: 0 20px 0 19px;
  }
  .has-media .comment-bar { height: 67px; }
  .comment-placeholder { font-family: Arial, sans-serif; font-size: 15px; color: #3a3a3a; }
  .comment-tools { display: flex; gap: 14px; }

  .loader { position: absolute; left: 478px; top: 1755px; width: 112px; height: 112px; }
  .loader-label {
    position: absolute; left: 0; top: 0; width: 112px; height: 112px;
    display: flex; align-items: center; justify-content: center;
    font-size: 15px; font-weight: 700; color: #222;
  }

  .site-footer {
    position: absolute; left: 0; top: 2164px; width: 1200px; height: 89px;
    background: var(--bar-bg); color: var(--footer-ink);
    font-size: 15px; text-align: center; padding-top: 31px;
  }
</style>
</head>
<body>

<header class="top-bar">
  <div class="brand">Pebble Tracks</div>
  <div class="account">
    <span class="account-name">THEO MARLOW</span>
    <div class="account-avatar" role="img" aria-label="Profile photo of Theo Marlow"></div>
    <div class="add-button">
      <svg width="20" height="20" viewBox="0 0 20 20"><path d="M10 2v16M2 10h16" stroke="#fff" stroke-width="4" stroke-linecap="round"/></svg>
    </div>
  </div>
</header>

<svg width="0" height="0" style="position:absolute">
  <defs>
    <symbol id="icon-like" viewBox="0 0 16 16"><path d="M1 7h3v8H1zM5 7l3-6c1.5 0 2 1 1.7 2.5L9.3 6H14c1 0 1.6.9 1.3 1.8l-1.8 6c-.2.7-.8 1.2-1.5 1.2H5z" fill="currentColor"/></symbol>
    <symbol id="icon-comment" viewBox="0 0 16 16"><path d="M8 1.5c4 0 7.2 2.5 7.2 5.6S12 12.7 8 12.7c-.8 0-1.5-.1-2.2-.3L2.2 14.5l1-3C1.7 10.4.8 8.8.8 7.1.8 4 4 1.5 8 1.5z" fill="currentColor"/></symbol>
    <symbol id="icon-share" viewBox="0 0 16 16"><circle cx="12.5" cy="3" r="2.6" fill="currentColor"/><circle cx="3.5" cy="8" r="2.6" fill="currentColor"/><circle cx="12.5" cy="13" r="2.6" fill="currentColor"/><path d="M12.5 3L3.5 8l9 5" stroke="currentColor" stroke-width="1.6" fill="none"/></symbol>
    <symbol id="icon-link" viewBox="0 0 16 16"><path d="M6.5 9.5l3-3M7 4.5l1.5-1.5a2.5 2.5 0 013.5 3.5L10.5 8M9 11.5L7.5 13A2.5 2.5 0 014 9.5L5.5 8" stroke="currentColor" stroke-width="1.6" fill="none" stroke-linecap="round"/></symbol>
    <symbol id="icon-smile" viewBox="0 0 16 16"><circle cx="8" cy="8" r="6.5" stroke="currentColor" stroke-width="1.3" fill="none"/><circle cx="5.8" cy="6.5" r=".9" fill="currentColor"/><circle cx="10.2" cy="6.5" r=".9" fill="currentColor"/><path d="M5 9.5c1.5 2 4.5 2 6 0" stroke="currentColor" stroke-width="1.3" fill="none"/></symbol>
  </defs>
</svg>

<main class="feed-panel">
  <h1 class="feed-title">FEED</h1>

  <div class="post-list">
    <article class="post">
      <div class="post-author">
        <div class="avatar tone-1" role="img" aria-label="Author profile photo"></div>
        <div class="author-info"><div class="author-name">THEO MARLOW</div><div class="post-meta">3 month ago . Sed ut perspiciatis unde omnis</div></div>
      </div>
      <p class="post-text">After I pour my morning cup of coffee, I will meditate for sixty seconds.</p>
      <div class="post-actions">
        <span class="action"><svg width="16" height="16"><use href="#icon-like"/></svg>Like</span>
        <span class="action"><svg width="16" height="16"><use href="#icon-comment"/></svg>Comments</span>
        <span class="action"><svg width="16" height="16"><use href="#icon-share"/></svg>Share</span>
      </div>
      <div class="comment-bar">
        <span class="comment-placeholder">Add Comment....</span>
        <span class="comment-tools" style="color:var(--icon-grey)"><svg width="16" height="16"><use href="#icon-link"/></svg><svg width="16" height="16"><use href="#icon-smile"/></svg></span>
      </div>
    </article>

    <article class="post has-media" style="margin-top:41px">
      <div class="post-author">
        <div class="avatar tone-2" role="img" aria-label="Author profile photo"></div>
        <div class="author-info"><div class="author-name">THEO MARLOW</div><div class="post-meta">3 month ago . Sed ut perspiciatis unde omnis</div></div>
      </div>
      <p class="post-text">After I meditate for sixty seconds, I will write my to-do list for the day.</p>
      <div class="post-media" role="img" aria-label="Photo of hands holding a glowing phone with social notification badges"></div>
      <div class="post-actions">
        <span class="action"><svg width="16" height="16"><use href="#icon-like"/></svg>Like</span>
        <span class="action"><svg width="16" height="16"><use href="#icon-comment"/></svg>Comments</span>
        <span class="action"><svg width="16" height="16"><use href="#icon-share"/></svg>Share</span>
      </div>
      <div class="comment-bar">
        <span class="comment-placeholder">Add Comment....</span>
        <span class="comment-tools" style="color:var(--icon-grey)"><svg width="16" height="16"><use href="#icon-link"/></svg><svg width="16" height="16"><use href="#icon-smile"/></svg></span>
      </div>
    </article>

    <article class="post" style="margin-top:45px">
      <div class="post-author">
        <div class="avatar tone-3" role="img" aria-label="Author profile photo"></div>
        <div class="author-info"><div class="author-name">THEO MARLOW</div><div class="post-meta">3 month ago . Sed ut perspiciatis unde omnis</div></div>
      </div>
      <p class="post-text">After I write my to-do list for the day, I will immediately begin my first task.</p>
      <div class="post-actions">
        <span class="action"><svg width="16" height="16"><use href="#icon-like"/></svg>Like</span>
        <span class="action"><svg width="16" height="16"><use href="#icon-comment"/></svg>Comments</span>
        <span class="action"><svg width="16" height="16"><use href="#icon-share"/></svg>Share</span>
      </div>
      <div class="comment-bar">
        <span class="comment-placeholder">Add Comment....</span>
        <span class="comment-tools" style="color:var(--icon-grey)"><svg width="16" height="16"><use href="#icon-link"/></svg><svg width="16" height="16"><use href="#icon-smile"/></svg></span>
      </div>
    </article>

    <article class="post" style="margin-top:52px">
      <div class="post-author">
        <div class="avatar tone-4" role="img" aria-label="Author profile photo"></div>
        <div class="author-info"><div class="author-name">THEO MARLOW</div><div class="post-meta">3 month ago . Sed ut perspiciatis unde omnis</div></div>
      </div>
      <p class="post-text">After I write my to-do list for the day, I will immediately begin my first task.</p>
      <div class="post-actions">
        <span class="action"><svg width="16" height="16"><use href="#icon-like"/></svg>Like</span>
        <span class="action"><svg width="16" height="16"><use href="#icon-comment"/></svg>Comments</span>
        <span class="action"><svg width="16" height="16"><use href="#icon-share"/></svg>Share</span>
      </div>
      <div class="comment-bar">
        <span class="comment-placeholder">Add Comment....</span>
        <span class="comment-tools" style="color:var(--icon-grey)"><svg width="16" height="16"><use href="#icon-link"/></svg><svg width="16" height="16"><use href="#icon-smile"/></svg></span>
      </div>
    </article>
  </div>

  <div class="loader">
    <svg width="112" height="112" viewBox="0 0 112 112" fill="#111">
      <circle cx="56" cy="8" r="9"/>
      <circle cx="32" cy="15" r="8"/>
      <circle cx="15" cy="32" r="7.5"/>
      <circle cx="8" cy="56" r="7"/>
      <circle cx="15" cy="80" r="6.5"/>
      <circle cx="32" cy="97" r="6"/>
      <circle cx="56" cy="104" r="5.5"/>
      <circle cx="80" cy="97" r="4.5"/>
      <circle cx="97" cy="80" r="3.5"/>
      <circle cx="104" cy="56" r="2.5"/>
      <circle cx="97" cy="32" r="1.8"/>
      <circle cx="80" cy="15" r="1.2"/>
    </svg>
    <div class="loader-label">LOADING</div>
  </div>
</main>

<footer class="site-footer">© Copyright -2018 Pebble Tracks.All rights reserved</footer>

</body>
</html>
```